Graphic design for a survey invitation campaign (3 assets)

Objective
Create an engaging and motivational graphic design for the "2024 KOVE Satisfaction Survey" campaign, aimed at encouraging the KOVE user community to share their insights and help shape the future of content.

FOCUS:
We need the graphics to be about creating the feeling of "Sharing your experience" and "Being heard", and not about taking the survey. Craft a visual narrative that encourages the KOVE user community to engage. This campaign seeks to transcend the mere act of taking a survey, focusing instead on the personal and collective impact of contributing insights.

DELIVERABLES
We need three assets using the same graphics:
1) a banner for our website (728 x 90 leaderboard banner)
2) a graph for a popup banner (Banner artwork is 33.5" x 90")
3) a postcard (4” x 6”)

COPY:
[Hero title] "Help Us Shape the Future of Content – Share Your KOVE Insights"
[Subtitle] The 2024 KOVE Satisfaction survey is ready. Join us to harness the collective experience of the KOVE user community.
[CTA] Take the Survey Now
Font: Poppins; convey professionalism. The main message should be prominent, with the subtext and CTA easily distinguishable.

Branding: Include the organization's logo and ensure the design aligns with brand guidelines to maintain consistency across the campaign.

Layout: Ensure a clean and organized layout with a clear hierarchy. The main message should capture immediate attention, followed by the subtext, and finally the CTA.

Visual and Stylistic Requirements: Imagery:
Use imagery that resonates with content creators and technical professionals. Consider incorporating abstract or symbolic representations of content creation, collaboration, and innovation.

Opt for visuals that represent diverse groups of professionals engaging in meaningful conversations. Elements such as open books, speech bubbles, or roundtable discussions can symbolize the sharing of knowledge and experiences.

Color Scheme: Opt for a professional yet inviting color palette. Use brand colors , supplemented by vibrant accents to highlight key elements like the CTA button.

Call to Action (CTA): Make the "Take the Survey Now!" button prominent and compelling. Use a contrasting color or design element to make it stand out.

Engagement Elements: Consider adding subtle animations or interactive elements (for digital formats) to make the CTA more engaging.

Design Inspirations:
Look at successful surveys and content strategy campaigns for inspiration, focusing on designs that effectively engage and motivate professional communities. Incorporate elements that symbolize growth, community, and insight, such as interconnected nodes or lightbulbs, to reflect the collective benefit of participating in the survey

Use our website for inspiration:
https://www.harborquillworks.com
Updates

Please see updates to the project brief for specific details on how to improve the designs. We appreciate your time and efforts.

Target Market(s)

KOVE users and professionals involved in content creation, management, and strategy. Individuals with experience in technical writing, documentation, and content strategy who are familiar with or interested in KOVE (Meridian Synthesis Module Layering).

Industry/Entity Type

We work in the technical documentation industry specializing in content data exchange model called KOVE.

Font styles to use
Sans Serif

Colors
0054AA
0677BA
7BADD7
CADEEF
E8F1F8
E54698
E96AAD
F1A4CE
F9D9EA
FCEFF6
6B429C
8869AF
B7A5CE
E3DAEB
F3F0F8

Requirements
Must have
• Copy for the Campaign: Main Message: "Help Us Shape the Future of Content – Share Your KOVE Insights" Subtext: "The 2024 KOVE Satisfaction survey is ready. Join us to harness the collective experience of the KOVE user community." Call to Action (CTA): "Take the Survey Now!"

```html
<!DOCTYPE html>
<html lang="en">
<head>
<meta charset="utf-8">
<title>KOVE Satisfaction Survey – Postcard</title>
<link href="https://fonts.googleapis.com/css2?family=Poppins:wght@400;500;600;700&display=swap" rel="stylesheet">
<style>
  :root{
    --page:#ebebeb;
    --sky:#58a4ee;
    --royal:#2b23a8;
    --navy:#22197c;
    --cyan:#2bc2f0;
    --white:#ffffff;
    --ink:#222222;
    --rule:#c9c9c9;
    --stamp:#e9e9e9;
  }
  *{margin:0;padding:0;box-sizing:border-box;}
  html,body{width:841px;height:1200px;overflow:hidden;background:var(--page);}
  body{position:relative;font-family:"Poppins",sans-serif;}

  .postcard{position:absolute;background:var(--white);overflow:hidden;}
  .postcard-front{left:71px;top:69px;width:685px;height:488px;}
  .postcard-back{left:75px;top:620px;width:679px;height:483px;}
  .card-shapes{position:absolute;inset:0;width:100%;height:100%;display:block;}

  .hero-title{
    position:absolute;left:22px;top:104px;width:300px;
    color:var(--white);font-weight:700;font-size:21px;line-height:28px;
  }
  .hero-subtitle{
    position:absolute;left:22px;top:228px;width:250px;
    color:var(--white);font-weight:500;font-size:10.6px;line-height:19.5px;
  }
  .cta-button{
    position:absolute;left:22px;top:317px;width:194px;height:35px;
    border-radius:18px;background:var(--royal);
    color:var(--white);font-weight:700;font-size:10.5px;
    display:flex;align-items:center;justify-content:center;
    text-transform:uppercase;letter-spacing:0.1px;
    box-shadow:0 4px 10px rgba(20,15,90,0.35);
  }

  .brand{position:absolute;left:48px;top:280px;display:flex;align-items:center;gap:18px;}
  .brand-dot{width:80px;height:80px;border-radius:50%;background:var(--white);}
  .brand-name{color:var(--white);font-weight:500;font-size:28px;line-height:32px;}

  .stamp-box{position:absolute;left:561px;top:20px;width:94px;height:94px;background:var(--stamp);}
  .address-line{position:absolute;left:398px;width:257px;height:1px;background:var(--rule);}
  .address-line.l1{top:172px;}
  .address-line.l2{top:226px;}
  .address-line.l3{top:280px;}

  .contact-heading{
    position:absolute;right:18px;top:324px;
    color:var(--ink);font-weight:700;font-size:17.5px;line-height:24px;
  }
  .contact-list{position:absolute;right:14px;top:362px;list-style:none;}
  .contact-item{
    display:flex;align-items:center;justify-content:flex-end;gap:13px;
    color:var(--ink);font-size:12.4px;line-height:19px;text-align:right;
    margin-bottom:12px;
  }
  .contact-item svg{width:20px;height:20px;flex:none;fill:var(--cyan);}
</style>
</head>
<body>

<section class="postcard postcard-front">
  <svg class="card-shapes" viewBox="0 0 509 363" preserveAspectRatio="none">
    <defs>
      <linearGradient id="scene-tones" x1="0" y1="0" x2="1" y2="1">
        <stop offset="0" stop-color="#e6e8ea"/>
        <stop offset="0.5" stop-color="#b9b3ad"/>
        <stop offset="1" stop-color="#d9dbdd"/>
      </linearGradient>
    </defs>
    <rect x="0" y="0" width="509" height="363" fill="url(#scene-tones)" role="img" aria-label="Photo of smiling colleagues shaking hands around a meeting table with a laptop"/>
    <path d="M0 0 H95 C170 30 215 110 210 200 C205 290 160 340 120 363 H0 Z" fill="var(--sky)"/>
    <path d="M112 363 C150 320 190 272 235 256 C272 268 292 320 298 363 Z" fill="var(--royal)"/>
  </svg>
  <h1 class="hero-title">Help Us Shape the<br>Future of Content –<br>Share Your KOVE<br>Insights</h1>
  <p class="hero-subtitle">The 2024 KOVE Satisfaction survey<br>is ready. Join us to harness the<br>collective experience of the<br>KOVE user community.</p>
  <div class="cta-button">Take the Survey Now</div>
</section>

<section class="postcard postcard-back">
  <svg class="card-shapes" viewBox="0 0 504 359" preserveAspectRatio="none">
    <circle cx="55" cy="-8" r="103" fill="var(--cyan)"/>
    <path d="M0 88 C40 100 70 140 120 145 C200 150 258 165 270 230 C282 295 262 335 232 359 H0 Z" fill="var(--navy)"/>
  </svg>

  <div class="brand">
    <span class="brand-dot"></span>
    <span class="brand-name">harborquill<br>works</span>
  </div>

  <div class="stamp-box"></div>
  <div class="address-line l1"></div>
  <div class="address-line l2"></div>
  <div class="address-line l3"></div>

  <h2 class="contact-heading">CONTACT US</h2>
  <ul class="contact-list">
    <li class="contact-item">
      <span>58 Linden Ave. Suite 410, Halifax,<br>NS B3H 1Z7 Canada</span>
      <svg viewBox="0 0 24 24"><path d="M12 2a7 7 0 0 0-7 7c0 5.2 7 13 7 13s7-7.8 7-13a7 7 0 0 0-7-7zm0 9.5A2.5 2.5 0 1 1 12 6.5a2.5 2.5 0 0 1 0 5z"/></svg>
    </li>
    <li class="contact-item">
      <span>+1 (902) 555-0147</span>
      <svg viewBox="0 0 24 24"><path d="M6.6 10.8a15.1 15.1 0 0 0 6.6 6.6l2.2-2.2a1 1 0 0 1 1-.25 11.4 11.4 0 0 0 3.6.57 1 1 0 0 1 1 1V20a1 1 0 0 1-1 1A17 17 0 0 1 3 4a1 1 0 0 1 1-1h3.5a1 1 0 0 1 1 1c0 1.25.2 2.45.57 3.57a1 1 0 0 1-.25 1z"/></svg>
    </li>
    <li class="contact-item">
      <span>hello@harborquillworks.com</span>
      <svg viewBox="0 0 24 24"><path d="M2 5h20v14H2z M2 5l10 8 10-8" fill="var(--cyan)"/><path d="M3 6l9 7 9-7" fill="none" stroke="#ffffff" stroke-width="1.6"/></svg>
    </li>
  </ul>
</section>

</body>
</html>
```